Web Design Project

We are an IT System Integrator. We provide Korvin 450 ERP System, CRM etc. We also provide hardware, networking servicing. Please look at www.zolvantix.com.sg. They provide the same service as us. We like to redesign our web site. I will attached the color that I prefer for reference.

Our website is www.tadurk.com.sg.  It has been created about 14 years ago.  We are trying to revamp it with a new look and information.   The new website must be informative, fast.    I have attached an attachment which show the color that I prefer(brownish golden).   

Our competitor (www.zolvantix.com) is carrying the same trade as us.  They have all the informations In their website that we will like to have.  Therefore I recommend you to take a look at my competitor website and have a better   
understanding on the kind of information I would like to have for my new website.

This project is guarantee to the person with the best design.  We can have it guarantee.

Target Market(s)

Corporate and companies

Industry/Entity Type

Hardware

```html
<!DOCTYPE html>
<html lang="en">
<head>
<meta charset="utf-8">
<title>Tadurk Information Systems</title>
<link href="https://fonts.googleapis.com/css2?family=Roboto:wght@400;500&family=Roboto+Condensed:wght@400&display=swap" rel="stylesheet">
<style>
:root{
  --gold-light:#c9972f;
  --gold-deep:#b07303;
  --gold-quote:#de9a17;
  --gold-text:#d88e10;
  --grey-band:#e6e6e6;
  --grey-text:#666;
  --grey-title:#555;
  --tile-grey:#8a8a8a;
  --white:#fff;
}
*{margin:0;padding:0;box-sizing:border-box}
html,body{width:1200px;height:1090px;overflow:hidden}
body{position:relative;background:var(--white);font-family:"Roboto",Arial,sans-serif;color:var(--grey-text)}
.abs{position:absolute}
.topbar{left:0;top:0;width:1200px;height:104px;background:var(--gold-light)}
.hero-band{left:0;top:104px;width:1200px;height:438px;background:var(--gold-deep)}
.brand{left:120px;top:0;width:198px;height:126px}
.brand-name{left:120px;top:30px;width:198px;text-align:center;font-size:34px;font-weight:500;color:var(--gold-deep);letter-spacing:1px}
.brand-tag{left:120px;top:88px;width:198px;text-align:center;font-size:10px;color:#555}
.nav{left:370px;top:40px;display:flex;list-style:none}
.nav li{color:var(--white);font-size:14.5px;font-weight:500;padding:0 23px;border-left:1px solid #a97a1f;line-height:25px}
.nav li:first-child{border-left:none}
.slider{left:120px;top:129px;width:960px;height:380px;background:linear-gradient(100deg,#e8eaee 0%,#c9ccd2 30%,#f4f4f4 55%,#3b3f4a 80%,#1f2330 100%);box-shadow:0 10px 14px -6px rgba(0,0,0,.45)}
.dots{left:580px;top:487px;display:flex;gap:5px}
.dots span{width:10px;height:10px;border-radius:50%;background:#999;border:1px solid #777}
.dots span.on{background:#333}
.quote{left:804px;top:190px;width:260px;height:235px;background:var(--gold-quote)}
.quote h2{position:absolute;left:14px;top:8px;font-family:"Roboto Condensed",sans-serif;font-weight:400;font-size:25px;color:var(--white)}
.field{position:absolute;left:10px;width:242px;height:34px;background:var(--white);border:2px solid #eee;border-radius:2px;font-family:"Roboto Condensed",sans-serif;font-size:13px;color:#555;padding:7px 9px}
.submit{position:absolute;left:160px;top:187px;width:91px;height:33px;background:linear-gradient(#555,#222);border-radius:3px;color:var(--white);font-family:"Roboto Condensed",sans-serif;font-size:17px;text-align:center;line-height:33px}
.partners{left:0;top:542px;width:1200px;height:103px;background:var(--grey-band)}
.partners-label{left:128px;top:580px;font-size:24px;font-weight:500;color:var(--gold-text)}
.divider-v{width:1px;height:50px;background:#bbb;top:567px}
.badge{top:568px;height:52px;background:var(--tile-grey);border-radius:4px}
.search{left:831px;top:576px;width:248px;height:31px;background:var(--white);border:1px solid #d0d0d0}
.intro-title{left:0;top:658px;width:1240px;text-align:center;font-size:26px;font-weight:500;color:var(--gold-text)}
.intro-text{left:130px;top:694px;width:940px;text-align:center;font-size:14.5px;font-weight:400;color:var(--grey-title);line-height:19px}
.rule{left:190px;top:747px;width:820px;height:1px;background:#ddd}
.card{top:768px;width:220px}
.card-media{width:220px;height:120px}
.card h3{margin-top:9px;font-size:19px;font-weight:400;color:var(--grey-title)}
.card p{margin-top:7px;font-size:12px;letter-spacing:-0.15px;line-height:15.5px;text-align:justify;color:var(--grey-text)}
.media-brand{background:var(--gold-light);display:flex;align-items:center;justify-content:center;color:var(--white);font-size:30px;font-weight:400;letter-spacing:2px}
.footer{left:0;top:1018px;width:1200px;height:72px;background:var(--gold-deep)}
.foot-links{left:117px;top:1034px;font-family:"Roboto Condensed",sans-serif;font-size:12px;color:var(--white)}
.foot-copy{left:117px;top:1058px;font-family:"Roboto Condensed",sans-serif;font-size:12px;color:var(--white)}
.social{left:882px;top:1041px;display:flex;gap:9px}
.social span{width:32px;height:32px;display:block}
</style>
</head>
<body>
<div class="abs topbar"></div>
<div class="abs hero-band"></div>

<svg class="abs brand" viewBox="0 0 198 126" aria-hidden="true"><polygon points="0,0 198,0 198,126 99,108 0,126" fill="#fff"/></svg>
<div class="abs brand-name">TADURK</div>
<div class="abs brand-tag">TADURK INFORMATION SYSTEMS</div>

<ul class="abs nav">
  <li>SOLUTIONS</li><li>HARDWARE</li><li>SERVICES</li><li>CLIENTS</li><li>ABOUT US</li><li>CONTACT US</li>
</ul>

<div class="abs slider" role="img" aria-label="Photo of business people shaking hands in an office"></div>
<div class="abs dots"><span></span><span class="on"></span><span></span></div>

<form class="abs quote">
  <h2>GET A QUOTE</h2>
  <div class="field" style="top:49px">Enter Your Name</div>
  <div class="field" style="top:95px">Enter Your Email</div>
  <div class="field" style="top:141px">Enter Your Phone</div>
  <div class="submit">SUBMIT</div>
</form>

<div class="abs partners"></div>
<div class="abs partners-label">PARTNERS</div>
<div class="abs divider-v" style="left:268px"></div>
<div class="abs badge" style="left:289px;width:60px"></div>
<div class="abs badge" style="left:370px;top:578px;width:95px;height:36px"></div>
<div class="abs badge" style="left:494px;top:580px;width:108px;height:30px"></div>
<div class="abs badge" style="left:625px;top:582px;width:88px;height:26px"></div>
<div class="abs badge" style="left:735px;top:562px;width:62px;height:62px;border-radius:50%"></div>
<div class="abs divider-v" style="left:815px"></div>
<div class="abs search">
  <svg class="abs" style="left:226px;top:8px" width="14" height="14" viewBox="0 0 14 14" aria-hidden="true"><circle cx="5.5" cy="5.5" r="4" fill="none" stroke="#aaa" stroke-width="1.6"/><line x1="8.5" y1="8.5" x2="13" y2="13" stroke="#aaa" stroke-width="2"/></svg>
</div>

<h1 class="abs intro-title">TADURK INFORMATION SYSTEMS</h1>
<p class="abs intro-text">BASED IN SINGAPORE WITH 11 YEARS OF ESTABLISHMENT, 250 LOCAL &amp; REGIONAL CUSTOMERS, 300 PROJECT IMPLEMENTATIONS, 1000 SATISFIED USERS AND WE ARE STILL GROWING.</p>
<div class="abs rule"></div>

<article class="abs card" style="left:120px">
  <div class="card-media media-brand">KORVIN</div>
  <h3>KORVIN CERTIFIED</h3>
  <p>Lorem ipsum dolor sit amet, consectetur adipisicing elit, sed do eiusmod tempor incididunt ut labore et dolore magna aliqua. Ut enim ad minim veniam</p>
</article>
<article class="abs card" style="left:366px">
  <div class="card-media" role="img" aria-label="Photo of two colleagues reviewing a document" style="background:linear-gradient(110deg,#f2f2f2,#cfcfcf 50%,#3a3f4c)"></div>
  <h3>SUCCESS STORIES</h3>
  <p>Lorem ipsum dolor sit amet, consectetur adipisicing elit, sed do eiusmod tempor incididunt ut labore et dolore magna aliqua. Ut enim ad minim veniam</p>
</article>
<article class="abs card" style="left:612px">
  <div class="card-media" role="img" aria-label="Photo of a business meeting at a laptop" style="background:linear-gradient(110deg,#9aa0a8,#2d2f35 55%,#bfc3c8)"></div>
  <h3>LATEST KORVIN 450</h3>
  <p>Lorem ipsum dolor sit amet, consectetur adipisicing elit, sed do eiusmod tempor incididunt ut labore et dolore magna aliqua. Ut enim ad minim veniam</p>
</article>
<article class="abs card" style="left:860px">
  <div class="card-media" role="img" aria-label="Photo of a team joining hands" style="background:linear-gradient(180deg,#eeeeee,#3a3a3a 70%,#222)"></div>
  <h3>SERVICES BEYOND</h3>
  <p>Lorem ipsum dolor sit amet, consectetur adipisicing elit, sed do eiusmod tempor incididunt ut labore et dolore magna aliqua. Ut enim ad minim veniam</p>
</article>

<footer class="abs footer"></footer>
<div class="abs foot-links">About us | Services &nbsp;| Contact</div>
<div class="abs foot-copy">© 2013 &nbsp;Tadurk Information Systems· All Rights Reserved</div>
<div class="abs social" aria-label="Social links">
  <span style="background:#3b5ba0" aria-label="Social link 1"></span>
  <span style="background:#1fb2e8" aria-label="Social link 2"></span>
  <span style="background:#d8262c" aria-label="Social link 3"></span>
  <span style="background:#c4161c" aria-label="Social link 4"></span>
  <span style="background:#dd4b39" aria-label="Social link 5"></span>
</div>
</body>
</html>
```